Harborline Benches business cards

I’d like a business card design that includes my logo, a tag line and my contact info. Black, textured background. My contact info color should match the orange and blue gradients. Tagline under logo: “Wooden Tables and Furniture of the Highest Quality”

Target Market(s)

High end furniture buyers

Contact Information for Business Card

Contact info, logo and tagline

```html
<!DOCTYPE html>
<html lang="en">
<head>
<meta charset="UTF-8">
<title>Harborline Benches – Business Cards</title>
<link href="https://fonts.googleapis.com/css2?family=Open+Sans:wght@400;600&family=Poppins:wght@400;600&display=swap" rel="stylesheet">
<style>
  :root {
    --stage: #2a2a2c;
    --card: #1e1f21;
    --orange: #f07a22;
    --blue: #1565c0;
    --ink: #f4f4f4;
    --rule: #6a6a6a;
    --pattern-light: #5a5a5c;
    --pattern-dark: #1a1a1b;
  }
  * { box-sizing: border-box; margin: 0; padding: 0; }
  html, body { width: 1200px; height: 1108px; overflow: hidden; background: var(--stage); }
  .stage { position: relative; width: 1200px; height: 1108px; }
  .card {
    position: absolute; top: 214px; width: 440px; height: 680px;
    border-radius: 24px; background: var(--card); overflow: hidden;
    box-shadow: 0 14px 30px rgba(0,0,0,.45);
  }
  .card--front { left: 120px; }
  .card--back { left: 640px; }

  .brand {
    position: absolute; left: 0; right: 0; top: 118px; text-align: center;
    font-family: "Open Sans", sans-serif;
  }
  .brand__name {
    display: inline-flex; align-items: center; gap: 12px;
    font-size: 34px; font-weight: 600; color: var(--orange); letter-spacing: .2px;
  }
  .brand__dot { width: 14px; height: 14px; border-radius: 50%; background: var(--orange); }
  .brand__tagline {
    margin-top: 14px; font-size: 13px; color: var(--ink); letter-spacing: .2px;
  }

  .person {
    position: absolute; left: 0; right: 0; top: 360px; text-align: center;
    font-family: "Poppins", sans-serif;
  }
  .person__name { font-size: 30px; font-weight: 600; color: var(--orange); line-height: 1.1; }
  .person__name .surname { color: var(--blue); }
  .person__role { font-size: 17px; color: var(--ink); margin-top: 2px; }

  .icon-row {
    position: absolute; left: 40px; right: 40px; top: 448px;
    display: flex; align-items: center; gap: 10px;
  }
  .icon-row__rule { flex: 1; height: 1px; background: var(--rule); }
  .icon-row__icons { display: flex; gap: 6px; }
  .icon-tile { width: 28px; height: 28px; border-radius: 4px; background: var(--orange);
    display: flex; align-items: center; justify-content: center; }

  .contact {
    position: absolute; left: 0; right: 0; top: 492px; text-align: center;
    font-family: "Poppins", sans-serif; color: var(--ink); font-size: 17px; line-height: 1.45;
  }
  .contact__rule { width: 240px; height: 1px; background: var(--rule); margin: 10px auto; }

  .back-pattern {
    position: absolute; inset: 0;
    background: linear-gradient(200deg, var(--pattern-light) 0%, #333335 40%, var(--pattern-dark) 85%);
  }
  .card--back .brand { top: 560px; }
</style>
</head>
<body>
<main class="stage">
  <section class="card card--front">
    <div class="brand">
      <div class="brand__name"><span class="brand__dot"></span>Harborline Benches</div>
      <p class="brand__tagline">Wooden Tables and Furniture of the Highest Quality</p>
    </div>

    <div class="person">
      <h1 class="person__name">Marcus <span class="surname">Ellery</span></h1>
      <p class="person__role">Managing Director</p>
    </div>

    <div class="icon-row">
      <span class="icon-row__rule"></span>
      <div class="icon-row__icons">
        <span class="icon-tile" aria-label="Phone">
          <svg width="16" height="16" viewBox="0 0 24 24"><path fill="#1e1f21" d="M6.6 10.8a15 15 0 0 0 6.6 6.6l2.2-2.2a1 1 0 0 1 1-.25 11.4 11.4 0 0 0 3.6.57 1 1 0 0 1 1 1V20a1 1 0 0 1-1 1A17 17 0 0 1 3 4a1 1 0 0 1 1-1h3.5a1 1 0 0 1 1 1c0 1.25.2 2.45.57 3.57a1 1 0 0 1-.25 1z"/></svg>
        </span>
        <span class="icon-tile" aria-label="Email">
          <svg width="16" height="16" viewBox="0 0 24 24"><rect x="3" y="6" width="18" height="12" fill="none" stroke="#1e1f21" stroke-width="2"/><path d="M3 6l9 7 9-7" fill="none" stroke="#1e1f21" stroke-width="2"/></svg>
        </span>
        <span class="icon-tile" aria-label="Website">
          <svg width="16" height="16" viewBox="0 0 24 24"><circle cx="12" cy="12" r="9" fill="none" stroke="#1e1f21" stroke-width="2"/><path d="M3 12h18M12 3c3 3 3 15 0 18M12 3c-3 3-3 15 0 18" fill="none" stroke="#1e1f21" stroke-width="1.6"/></svg>
        </span>
      </div>
      <span class="icon-row__rule"></span>
    </div>

    <div class="contact">
      <p>044-555 218 730</p>
      <p>hello@harborline.com</p>
      <p>www.harborline.com</p>
      <div class="contact__rule"></div>
      <p>88 Quayside Row, Dockside</p>
      <p>45180, Northmere</p>
    </div>
  </section>

  <section class="card card--back">
    <div class="back-pattern" role="img" aria-label="Repeating pattern of bare trees fading from grey to black"></div>
    <div class="brand">
      <div class="brand__name"><span class="brand__dot"></span>Harborline Benches</div>
    </div>
  </section>
</main>
</body>
</html>
```